BRIX GUARDING WEBSITE BANNER DESIGN OF AWESOME

Please take a look at the attached Banner. I want a redesign Idea. The requirements are below.

1)Must Use Website Background
2)Must Use Photo Provided
3)Must Include Button
4)Website the banner will be used on you can see the current at the bottom of the page: https://b.lunorvex.com

Target Market(s)

Anyone Seeking Security Guard Services

```html
<!DOCTYPE html>
<html lang="en">
<head>
<meta charset="utf-8">
<title>Brix Guarding – Website Banners</title>
<link href="https://fonts.googleapis.com/css2?family=Poppins:wght@600&family=Roboto:wght@500&display=swap" rel="stylesheet">
<style>
  :root{
    --canvas:#bcbcbc;
    --navy-deep:#173a66;
    --navy:#1b4a7a;
    --navy-light:#1f5285;
    --edge:#1a365e;
    --white:#ffffff;
    --amber:#fdb01a;
    --icon-ring:#a9b4c2;
    --icon-ink:#1c3f6b;
    --photo-a:#0f1c2e;
    --photo-b:#3c5a85;
    --brand-tint:#e8b27a;
  }
  *{box-sizing:border-box;margin:0;padding:0}
  html,body{width:1200px;height:864px;overflow:hidden;background:var(--canvas)}
  body{position:relative;font-family:"Roboto",Arial,sans-serif}
  .banner{position:absolute;left:75px;width:1050px;overflow:hidden;color:var(--white)}
  .banner--wide{top:83px;height:292px}
  .banner--tall{top:451px;height:330px}
  .banner__bg{position:absolute;inset:0}
  .copy{position:absolute}
  .title{font-family:"Poppins",Arial,sans-serif;font-weight:600;font-size:32px;line-height:1.1;white-space:nowrap}
  .tagline{font-size:16.5px;margin-top:4px;white-space:nowrap}
  .features{position:absolute;display:flex;list-style:none}
  .feature{display:flex;flex-direction:column;align-items:center;width:140px;font-size:13.5px;white-space:nowrap}
  .feature__icon{width:54px;height:54px;border-radius:50%;background:var(--white);border:4px solid var(--icon-ring);display:flex;align-items:center;justify-content:center;margin-bottom:12px}
  .cta{position:absolute;width:163px;height:41px;border-radius:21px;background:var(--amber);color:var(--white);font-weight:500;font-size:14.5px;display:flex;align-items:center;justify-content:center;gap:7px;text-decoration:none;letter-spacing:.2px}
  .photo-brand{font-family:"Roboto",Arial,sans-serif;font-weight:500;font-size:15px;fill:var(--brand-tint);letter-spacing:1.5px}
</style>
</head>
<body>

<svg width="0" height="0" style="position:absolute">
  <defs>
    <linearGradient id="photoTone" x1="0" y1="1" x2="1" y2="0">
      <stop offset="0" stop-color="var(--photo-a)"/>
      <stop offset=".55" stop-color="#22375a"/>
      <stop offset="1" stop-color="var(--photo-b)"/>
    </linearGradient>
    <symbol id="ico-person" viewBox="0 0 24 24"><g fill="none" stroke="var(--icon-ink)" stroke-width="1.3"><circle cx="12" cy="8" r="4"/><path d="M4 22c0-5 3.5-7.5 8-7.5s8 2.5 8 7.5z"/><path d="M12 14.5v7.5"/></g></symbol>
    <symbol id="ico-clock" viewBox="0 0 24 24"><g fill="none" stroke="var(--icon-ink)" stroke-width="1.3"><path d="M20.5 12a8.5 8.5 0 1 1-2.5-6"/><path d="M18.5 2.5v3.8h-3.8"/><circle cx="12" cy="12" r="6.3"/></g><text x="12" y="13.8" font-size="5" text-anchor="middle" fill="var(--icon-ink)" font-family="Roboto,Arial,sans-serif">24/7</text></symbol>
    <symbol id="ico-contract" viewBox="0 0 24 24"><g fill="none" stroke="var(--icon-ink)" stroke-width="1.3"><path d="M6 2h9l4 4v11H6z"/><path d="M8.5 7h6M8.5 10h8M8.5 13h5"/><path d="M4 19l4-2 3 2 3-2 4 2-3 3h-8z"/></g></symbol>
    <symbol id="ico-arrow" viewBox="0 0 16 16"><circle cx="8" cy="8" r="8" fill="var(--white)"/><path d="M6.5 4.5 10 8l-3.5 3.5" fill="none" stroke="var(--amber)" stroke-width="2.2"/></symbol>
  </defs>
</svg>

<!-- Banner one: copy left, photo right -->
<section class="banner banner--wide">
  <svg class="banner__bg" width="1050" height="292" viewBox="0 0 1050 292">
    <rect width="1050" height="292" fill="var(--navy)"/>
    <polygon points="0,0 53,0 6,124 0,124" fill="var(--edge)"/>
    <polygon points="0,124 600,124 560,292 0,292" fill="var(--navy-deep)"/>
    <polygon points="53,0 600,0 560,124 6,124" fill="var(--navy-light)"/>
    <polygon points="250,200 420,292 120,292" fill="var(--navy)" opacity=".5"/>
    <polygon points="606,0 1050,0 1050,292 606,292 535,146" fill="var(--white)"/>
    <g role="img" aria-label="Photo of a security guard in a dark jacket shining a flashlight up a stairwell">
      <polygon points="613,0 1050,0 1050,292 613,292 544,146" fill="url(#photoTone)"/>
      <text class="photo-brand" x="950" y="80" text-anchor="middle">BRIX GUARDING</text>
    </g>
  </svg>
  <div class="copy" style="left:97px;top:25px">
    <h1 class="title">Get Secured Today</h1>
    <p class="tagline">We take your security personal.</p>
  </div>
  <ul class="features" style="left:64px;top:110px">
    <li class="feature"><span class="feature__icon"><svg width="28" height="28"><use href="#ico-person"/></svg></span>Client Portal</li>
    <li class="feature"><span class="feature__icon"><svg width="30" height="30"><use href="#ico-clock"/></svg></span>24x7 Dispatch</li>
    <li class="feature" style="margin-left:6px"><span class="feature__icon"><svg width="28" height="28"><use href="#ico-contract"/></svg></span>No Binding Contracts</li>
  </ul>
  <a class="cta" href="https://b.lunorvex.com" style="left:97px;top:220px">GET STARTED <svg width="14" height="14"><use href="#ico-arrow"/></svg></a>
</section>

<!-- Banner two: photo left, copy right -->
<section class="banner banner--tall">
  <svg class="banner__bg" width="1050" height="330" viewBox="0 0 1050 330">
    <rect width="1050" height="330" fill="var(--navy)"/>
    <polygon points="0,0 60,0 0,150" fill="var(--edge)"/>
    <polygon points="470,143 1000,143 1050,40 1050,330 470,330" fill="var(--navy-deep)"/>
    <polygon points="996,0 1050,0 1050,40 1000,143" fill="var(--edge)"/>
    <polygon points="470,0 996,0 950,143 470,143" fill="var(--navy-light)"/>
    <polygon points="800,230 1050,330 860,330" fill="var(--navy)" opacity=".5"/>
    <path d="M150,0 H445 L492,164 L445,330 H150 Q-150,165 150,0Z" fill="var(--white)"/>
    <g role="img" aria-label="Photo of a security guard in a dark jacket shining a flashlight up a stairwell">
      <path d="M158,0 H438 L484,164 L438,330 H158 Q-136,165 158,0Z" fill="url(#photoTone)"/>
      <text class="photo-brand" x="345" y="72" text-anchor="middle">BRIX GUARDING</text>
    </g>
  </svg>
  <div class="copy" style="left:735px;top:40px;transform:translateX(-50%);text-align:center">
    <h1 class="title">Get Secured Today</h1>
    <p class="tagline">We take your security personal.</p>
  </div>
  <ul class="features" style="left:522px;top:128px">
    <li class="feature"><span class="feature__icon"><svg width="28" height="28"><use href="#ico-person"/></svg></span>Client Portal</li>
    <li class="feature"><span class="feature__icon"><svg width="30" height="30"><use href="#ico-clock"/></svg></span>24x7 Dispatch</li>
    <li class="feature" style="margin-left:6px"><span class="feature__icon"><svg width="28" height="28"><use href="#ico-contract"/></svg></span>No Binding Contracts</li>
  </ul>
  <a class="cta" href="https://b.lunorvex.com" style="left:654px;top:239px">GET STARTED <svg width="14" height="14"><use href="#ico-arrow"/></svg></a>
</section>

</body>
</html>
```